FinTech company looking to revamp and expand client-facing interface for our financial models

Pellworth Engines currently has a very simple website that allows clients to interact with our financial models. We are looking to completely redesign the current site and add several extra pages to provide extra functionality. We want the design to have a modern, slick feel, that will work on both a desktop or a tablet. It should be straightforward for clients to move between different pages at any time, and clear from the layout how to interact with the more advanced features. We have included screenshots of existing pages in the attached design brief, as well as sketches of the functionality required by the new pages, but can't provide a direct link to the current site.
Target Market(s)
Professional investors that will be paying to access the interface
Industry/Entity Type
Finance
Number of Pages Required
4 page
Colors
Designer to choose colors to be used in the design.
Look and feel
Each slider illustrates characteristics of the customer's brand and the style your logo design should communicate.

```html
<!DOCTYPE html>
<html lang="en">
<head>
<meta charset="utf-8">
<title>Pellworth Engines – Backtest</title>
<link rel="stylesheet" href="https://fonts.googleapis.com/css2?family=Open+Sans:wght@400;600;700&family=Roboto+Condensed:wght@400;700&display=swap">
<style>
:root{
  --navy:#0b2f63;
  --teal:#036b63;
  --page:#ececec;
  --white:#ffffff;
  --ink:#111111;
  --overlay:rgba(38,38,38,0.93);
  --line:#d9d9d9;
  --stripe:#f1f1f1;
  --grey-head:#707070;
  --scroll:#cfcfcf;
  --dot-blue:#3b6db3;
  --dot-olive:#b8b82c;
  --dot-green:#4d9a3a;
}
*{box-sizing:border-box;margin:0;padding:0}
html,body{width:1200px;height:1122px;overflow:hidden;background:var(--white)}
body{font-family:"Open Sans",sans-serif;color:var(--ink)}
.stage{position:absolute;left:0;top:0;width:1300px;height:1215px;transform:scale(0.923077);transform-origin:0 0;background:var(--white)}
.abs{position:absolute}
.page{left:15px;top:15px;width:1270px;height:1185px;background:var(--page)}
/* nav */
.nav{left:15px;top:15px;width:1270px;height:60px;background:var(--white);display:flex;font-weight:700;font-size:14px}
.nav-item{height:60px;display:flex;align-items:center;justify-content:center;gap:8px;border-right:1px solid #e6e6e6}
.brand{width:180px;font-size:19px}
.range{width:90px}
.spacer{width:135px}
.nav-right{margin-left:auto;display:flex}
.nav-right .nav-item{padding:0 24px;font-size:13px}
.nav-item.active{background:var(--navy);color:var(--white)}
/* chart card */
.chart-card{left:105px;top:115px;width:1160px;height:425px;background:var(--white);box-shadow:0 2px 8px rgba(0,0,0,.08)}
.chart-band{left:105px;top:115px;width:1160px;height:85px;background:#efefef}
.legend{left:1145px;top:253px;font-family:serif;font-size:12px}
/* tables */
.stats{left:105px;top:630px;width:400px;height:490px;background:var(--white)}
.trades{left:545px;top:630px;width:720px;height:490px;background:var(--white)}
.thead{height:70px;background:#1b1b1b;color:var(--white);font-family:"Open Sans",sans-serif;font-weight:600;font-size:16px}
.row{display:flex;height:69px;align-items:center;font-family:"Roboto Condensed",sans-serif;font-size:17px}
.row:nth-child(even){background:var(--stripe)}
.cell{width:180px;text-align:center;border-right:1px solid #e2e2e2;height:100%;display:flex;align-items:center;justify-content:center}
.vbar{position:absolute;right:0;top:70px;width:40px;bottom:0;background:#d6d6d6}
.vbar i{position:absolute;left:11px;top:25px;width:18px;bottom:25px;background:var(--white);border-radius:9px}
.vbar b{position:absolute;left:11px;top:25px;width:18px;height:74px;background:#9a9a9a;border-radius:9px}
.export{left:1175px;top:593px;color:var(--navy);font-weight:700;font-size:17px;display:flex;gap:8px;align-items:center}
/* overlay */
.overlay{left:15px;top:155px;width:900px;height:755px;background:var(--overlay)}
.options-tab{left:915px;top:408px;width:50px;height:222px;background:#2a2a2a}
.options-label{left:916px;top:520px;color:var(--white);font-weight:600;font-size:17px;letter-spacing:1px;transform:rotate(-90deg);transform-origin:left top;white-space:nowrap}
.faint-tabs{left:160px;top:165px;display:flex;font-size:13px;color:#4a4a4a;font-weight:600}
.faint-tabs span{width:95px;height:35px;display:flex;align-items:center;justify-content:center}
.mode{top:230px;width:180px;height:45px;display:flex;align-items:center;justify-content:center;color:var(--white);font-size:17px;font-weight:600;border:2px solid var(--white);border-bottom:none;border-radius:4px 4px 0 0}
.mode.on{left:280px;background:var(--navy);border-bottom:2px solid var(--white)}
.mode.off{left:470px}
.panel{top:305px;width:370px;height:530px;background:var(--white)}
.models{left:75px}
.params{left:485px}
.search{display:flex;gap:10px;padding:10px 17px;height:50px;border-bottom:1px solid var(--line)}
.search .field{width:181px;height:31px;border:2px solid #ddd;border-radius:3px;font-size:15px;padding:4px 11px}
.btn-select{width:105px;height:30px;background:var(--teal);color:var(--white);font-weight:700;font-size:15px;display:flex;align-items:center;justify-content:center;border-radius:2px}
.list{position:relative;height:400px}
.model{height:49px;display:flex;align-items:center;padding-left:21px;font-size:17px;font-weight:700;border-bottom:1px solid var(--line);width:330px}
.model.sel{background:var(--teal);color:var(--white)}
.list .track{position:absolute;left:330px;top:0;width:40px;height:400px;background:var(--scroll)}
.list .track i{position:absolute;left:10px;top:25px;width:18px;height:350px;background:var(--white);border-radius:9px;border:1px solid #bbb}
.list .track b{position:absolute;left:10px;top:25px;width:18px;height:75px;background:#9a9a9a;border-radius:9px}
.btn-add{position:absolute;left:88px;top:470px;width:194px;height:40px;background:var(--navy);color:var(--white);font-weight:700;font-size:13px;display:flex;align-items:center;justify-content:center;gap:12px;border-radius:3px}
.params-head{height:50px;background:var(--grey-head);color:var(--white);font-weight:700;font-size:17px;display:flex;align-items:center;justify-content:center}
.param{height:50px;display:flex;align-items:center;padding-left:18px;border-bottom:1px solid var(--line)}
.param label{width:96px;font-weight:700;font-size:17px}
.param .field{width:242px;height:31px;border:2px solid #ddd;border-radius:3px;font-size:15px;padding:4px 11px}
.btn-run{position:absolute;left:109px;top:466px;width:153px;height:48px;background:var(--navy);color:var(--white);font-weight:700;font-size:16px;display:flex;align-items:center;justify-content:center;border-radius:3px}
</style>
</head>
<body>
<div class="stage">
  <div class="abs page"></div>

  <nav class="abs nav">
    <div class="nav-item brand">KESTREL</div>
    <div class="nav-item range">250D</div>
    <div class="nav-item range">83D</div>
    <div class="nav-item range">42D</div>
    <div class="nav-item spacer"></div>
    <div class="nav-right">
      <div class="nav-item"><svg width="24" height="22" viewBox="0 0 24 22"><path d="M2 11 12 2l10 9M5 9v11h5v-6h4v6h5V9" fill="none" stroke="#111" stroke-width="2.4"/></svg>MODELS</div>
      <div class="nav-item"><svg width="24" height="24" viewBox="0 0 24 24" fill="#333"><circle cx="12" cy="12" r="3"/><circle cx="12" cy="3" r="1.6"/><circle cx="12" cy="21" r="1.6"/><circle cx="3" cy="12" r="1.6"/><circle cx="21" cy="12" r="1.6"/><circle cx="5.6" cy="5.6" r="1.6"/><circle cx="18.4" cy="18.4" r="1.6"/><circle cx="5.6" cy="18.4" r="1.6"/><circle cx="18.4" cy="5.6" r="1.6"/></svg>SENSITIVITIES</div>
      <div class="nav-item"><svg width="24" height="24" viewBox="0 0 24 24" fill="none" stroke="#111" stroke-width="2"><circle cx="6" cy="6" r="4"/><circle cx="18" cy="6" r="4"/><circle cx="6" cy="18" r="4"/><circle cx="18" cy="18" r="4"/></svg>PORTFOLIO</div>
      <div class="nav-item active"><svg width="26" height="22" viewBox="0 0 26 22" fill="none" stroke="#fff" stroke-width="2"><rect x="1" y="1" width="24" height="20"/><path d="M5 16l5-6 4 4 7-8"/></svg>BACKTEST</div>
    </div>
  </nav>

  <div class="abs chart-card"></div>
  <div class="abs chart-band"></div>
  <svg class="abs" style="left:105px;top:200px" width="1160" height="300">
    <g stroke="#eee"><line x1="60" y1="63" x2="1005" y2="63"/><line x1="60" y1="100" x2="1005" y2="100"/><line x1="60" y1="137" x2="1005" y2="137"/><line x1="60" y1="175" x2="1005" y2="175"/><line x1="60" y1="212" x2="1005" y2="212"/></g>
    <line x1="60" y1="249" x2="1005" y2="249" stroke="#999"/>
    <line x1="505" y1="63" x2="960" y2="63" stroke="var(--dot-blue)" stroke-width="7" stroke-dasharray="6 3"/>
    <line x1="820" y1="68" x2="930" y2="68" stroke="var(--dot-olive)" stroke-width="5" stroke-dasharray="6 3"/>
    <circle cx="930" cy="246" r="4" fill="var(--dot-green)"/><circle cx="938" cy="246" r="4" fill="var(--dot-green)"/>
    <text x="785" y="275" font-size="12" fill="#555">May 2019</text>
    <text x="930" y="275" font-size="12" fill="#555">Jul 2019</text>
    <g>
      <circle cx="1045" cy="62" r="3.5" fill="#8fb3d9"/><circle cx="1045" cy="80" r="3.5" fill="#f5a65b"/><circle cx="1045" cy="99" r="3.5" fill="#4d9a3a"/><circle cx="1045" cy="118" r="3.5" fill="#e0707a"/><circle cx="1045" cy="136" r="3.5" fill="#b59bd6"/><circle cx="1045" cy="155" r="3.5" fill="#b08f85"/><circle cx="1045" cy="173" r="3.5" fill="#e89ccf"/><circle cx="1045" cy="192" r="3.5" fill="#aaa"/><circle cx="1045" cy="210" r="3.5" fill="#b8b82c"/><circle cx="1045" cy="229" r="3.5" fill="#6cc7d8"/><circle cx="1045" cy="247" r="3.5" fill="#2f5fa8"/>
    </g>
  </svg>
  <div class="abs legend">Names</div>

  <div class="abs export"><svg width="26" height="22" viewBox="0 0 26 22" fill="none" stroke="#0b2f63" stroke-width="2.2"><path d="M12 4H2v16h18v-8"/><path d="M9 14c2-6 7-8 13-8M18 2l4 4-4 4"/></svg>Export</div>

  <section class="abs stats">
    <div class="thead"></div>
    <div class="row"><div class="cell">Stat 1</div><div class="cell">0.5</div></div>
    <div class="row"><div class="cell">Stat 2</div><div class="cell">-3</div></div>
    <div class="row"><div class="cell">Stat 3</div><div class="cell">30%</div></div>
    <div class="row"><div class="cell">Stat 4</div><div class="cell">0.5</div></div>
    <div class="row"><div class="cell">Stat 5</div><div class="cell">-3</div></div>
    <div class="row"><div class="cell">Stat 6</div><div class="cell">30%</div></div>
    <div class="vbar"><i></i></div>
  </section>

  <section class="abs trades">
    <div class="thead row" style="background:#1b1b1b;height:70px"><div class="cell">Entry</div><div class="cell">Exit</div><div class="cell" style="font-family:'Open Sans',sans-serif;font-weight:600">Size</div><div class="cell" style="font-family:'Open Sans',sans-serif;font-weight:600">Return</div></div>
    <div class="row" style="background:var(--white)"><div class="cell">2018-04-05</div><div class="cell">2018-04-07</div><div class="cell">13</div><div class="cell">5%</div></div>
    <div class="row"><div class="cell">2018-04-05</div><div class="cell">2018-04-07</div><div class="cell">12</div><div class="cell">7%</div></div>
    <div class="row" style="background:var(--white)"><div class="cell">2018-04-05</div><div class="cell">2018-04-07</div><div class="cell">15</div><div class="cell">6%</div></div>
    <div class="row"><div class="cell">2018-04-05</div><div class="cell">2018-04-07</div><div class="cell">16</div><div class="cell">9%</div></div>
    <div class="row" style="background:var(--white)"><div class="cell">2018-04-05</div><div class="cell">2018-04-07</div><div class="cell">12</div><div class="cell">8%</div></div>
    <div class="row"><div class="cell">2018-04-05</div><div class="cell">2018-04-07</div><div class="cell">19</div><div class="cell">6%</div></div>
    <div class="vbar"><i></i><b></b></div>
  </section>

  <div class="abs overlay"></div>
  <div class="abs faint-tabs"><span style="background:#1f242c;width:155px">CHART</span><span>#1</span><span>#2</span><span>#3</span><span style="background:#1c1c1c">#4</span></div>
  <div class="abs options-tab"></div>
  <div class="abs options-label">OPTIONS</div>
  <svg class="abs" style="left:950px;top:518px" width="30" height="30" viewBox="0 0 30 30"><circle cx="15" cy="15" r="13" fill="var(--navy)" stroke="#fff" stroke-width="2"/><path d="M21 15H9m5-5-5 5 5 5" fill="none" stroke="#fff" stroke-width="2.4"/></svg>

  <div class="abs mode on">Mode 1</div>
  <div class="abs mode off">Mode 2</div>

  <section class="abs panel models">
    <div class="search"><div class="field">Model name</div><div class="btn-select">Select</div></div>
    <div class="list">
      <div class="model">Model 1</div><div class="model">Model 2</div><div class="model sel">Model 3</div><div class="model">Model 4</div><div class="model">Model 5</div><div class="model">Model 6</div><div class="model">Model 7</div><div class="model">Model 8</div>
      <div class="track"><i></i><b></b></div>
    </div>
    <div class="btn-add"><svg width="22" height="22" viewBox="0 0 22 22" fill="none" stroke="#fff" stroke-width="1.8"><circle cx="11" cy="11" r="9.5"/><path d="M11 6v10M6 11h10"/></svg>ADD A MODEL</div>
  </section>

  <section class="abs panel params">
    <div class="params-head">Parameters:</div>
    <div class="param"><label>Entry:</label><div class="field">0.5</div></div>
    <div class="param"><label>Exit:</label><div class="field">-0.3</div></div>
    <div class="param"><label>Lookback:</label><div class="field">5</div></div>
    <div class="param"><label>Entry:</label><div class="field">0.5</div></div>
    <div class="param"><label>Exit:</label><div class="field">-0.3</div></div>
    <div class="param"><label>Lookback:</label><div class="field">5</div></div>
    <div class="param"><label>Entry:</label><div class="field">0.5</div></div>
    <div class="param"><label>Exit:</label><div class="field">-0.3</div></div>
    <div class="btn-run">RUN</div>
  </section>

  <svg class="abs" style="left:196px;top:486px" width="30" height="38" viewBox="0 0 30 38"><path d="M8 3c0-2 4-2 4 0v13c0-2 4-2 4 0v2c0-2 4-2 4 0v2c0-2 4-2 4 0v8c0 5-3 8-8 8h-2c-4 0-6-2-8-5L2 24c-1-2 2-4 4-2l2 3z" fill="#fff" stroke="#111" stroke-width="1.6"/></svg>
</div>
</body>
</html>
```